Announcement for a New Trauma Therapy Group - Rack Card

I need a two-sided "rack" card that is 4x9 announcing a Women's Trauma and Loss Group. I am a licensed therapist and will be starting this support group for women who have experienced trauma of all kinds. In addition to groups, I offer individual, couples, and family counseling sessions.

I would like to see designs that are soft tones and use colors like muted blues, greens, and sand tones. The final design should communicate hope and healing as well as have a peaceful feel to it.

I would like a picture of a woman's profile from either the side or from behind her. (possibly a contemplative picture on a beach)

I am attaching a picture of myself to go alongside the bio information as well.

On One Side, I need the description of the group and contact info:

Mending the Weary Spirit
Women's Trauma & Loss Group
Led by Licensed Professional Counselor, Lena Marsh Pruitt

10 Week Group
Cost - $35 session
Group size limited to 10 participants

Topics Include:
What is Trauma?
How Trauma Affects Us
Creating a Feeling of Safety
Managing Trauma Triggers
Importance of Self Care
Healthy vs. Unhealthy Coping
Guilt, Shame, and Blame
Victim vs. Victimized
Grieving through Loss
Anger and Forgiveness
Imagining a Better Future

For More Information, Contact:
Lena Marsh Pruitt, LPC, LMFT
(555) 318-4926
lena@calmwatersguide.example

On Side Two:

Life hurts and does not seem fair. So what do you do when you are faced with an event in your life that knocks you off your feet? It seems no one understands what you are feeling and no one knows just what to say. It is tempting to pull away and isolate or put up a mask and pretend everything is OK.

It is my desire you know that you are not alone! There are others who understand the feelings you are going through and offer a safe place for encouraging support. I want to invite you to embark on a courageous journey of healing where you will not only learn how to "survive" after trauma and loss, but instead, learn that you can once again "thrive"!
- Lena Marsh Pruitt, LPC, LMFT

Lena Marsh Pruitt is a Licensed Professional Counselor and Licensed Marriage and Family Therapist. She is the owner of Quiet Harbor Counseling Services located in Tulsa, OK.

Lena is a trauma survivor herself and understands firsthand the unique challenges that can arise on the journey to healing.

(Include Lena's picture next to bio)

(Attach logo and business information to this side as well.)

Target Market(s)

Women who have gone through a traumatic experience or loss and are hurting emotionally

Industry/Entity Type

Counsellor

Font styles to use
Serif
Script

Colors
fbe7d2
86cfc6
cfeae6
85abd2
cfdeed

Requirements
Must have
• Lena's picture as well as her logo and contact information must be on the card.
• One side of the card should describe the group with the following description:
• "Mending the Weary Spirit"
• Women's Trauma & Loss Group
• Led by Licensed Professional Counselor, Lena Marsh Pruitt
• 10 Week Group
• Cost - $35 session
• Group size limited to 10 participants
• Topics Include:
• What is Trauma?
• How Trauma Affects Us
• Creating a Feeling of Safety
• Managing Trauma Triggers
• Importance of Self Care
• Healthy vs. Unhealthy Coping
• Guilt, Shame, and Blame
• Victim vs. Victimized
• Grieving through Loss
• Anger and Forgiveness
• Imagining a Better Future
• For More Information, Contact:
• Lena Marsh Pruitt, LPC, LMFT
• (555) 318-4926
• lena@calmwatersguide.example
• On the second side, it must have this note from Lena:
• Life hurts and does not seem fair. So what do you do when you are faced with an event in your life that knocks you off your feet? It seems no one understands what you are feeling and no one knows just what to say. It is tempting to pull away and isolate or put up a mask and pretend everything is OK.
• It is my desire you know that you are not alone! There are others who understand the feelings you are going through and offer a safe place for encouraging support. I want to invite you to embark on a courageous journey of healing where you will not only learn how to "survive" after trauma and loss, but instead, learn that you can once again "thrive"!
• - Lena Marsh Pruitt, LPC, LMFT
• Lena Marsh Pruitt is a Licensed Professional Counselor and Licensed Marriage and Family Therapist. She is the owner of Quiet Harbor Counseling Services located in Tulsa, OK.
• Lena is a trauma survivor herself and understands firsthand the unique challenges that can arise on the journey to healing. In addition to facilitating groups, Lena also offers individual, marriage, and family counseling.
Nice to have
• soft muted colors that are peaceful. Light blues, greens, sand colors would work well. A picture at the top of the card of either a woman or a woman's profile that is hopeful such as a woman sitting at a beach overlooking the ocean.
Should not have
• No harsh or bright bold colors. This card needs to have a peaceful feeling to it.

```html
<!DOCTYPE html>
<html lang="en">
<head>
<meta charset="utf-8">
<title>Mending the Weary Spirit – Rack Card</title>
<link href="https://fonts.googleapis.com/css2?family=Montserrat:wght@400;500;600;700&family=Playball&family=Roboto+Condensed:wght@300;400&display=swap" rel="stylesheet">
<style>
  :root{
    --page:#f1f0ec;
    --ink:#1e1e1e;
    --teal:#86cfc6;
    --mint:#cfeae6;
    --mint-card:#d4ece9;
    --blue:#85abd2;
    --blue-deep:#7499c4;
    --blue-pale:#cfdeed;
    --sand:#fbe7d2;
    --green:#3f7a2a;
    --green-text:#4f8a2e;
    --white:#ffffff;
  }
  *{box-sizing:border-box;margin:0;padding:0}
  html,body{width:1200px;height:1200px;overflow:hidden}
  body{background:var(--page);font-family:"Montserrat",sans-serif;color:var(--ink);position:relative}
  .card{position:absolute;top:37px;width:500px;height:1125px;overflow:hidden;box-shadow:0 6px 22px rgba(0,0,0,.12)}
  .card--front{left:70px;background:var(--white)}
  .card--back{left:630px;background:var(--mint-card)}
  .abs{position:absolute}

  /* front */
  .hero-photo{left:0;top:0;width:500px;height:470px;
    background:linear-gradient(180deg,#c9dcea 0%,#e3ecf2 38%,#dfe6ea 62%,#8fa8b6 66%,#7d97a6 86%,#b9ab98 94%,#a99885 100%)}
  .hero-curve{left:0;top:405px;width:500px;height:70px}
  .brand{left:0;width:500px;top:70px;display:flex;justify-content:center;align-items:center;gap:10px}
  .brand__dot{width:34px;height:34px;border-radius:50%;background:var(--green)}
  .brand__name{font-weight:600;color:var(--green);font-size:21px;line-height:1.15}
  .title{font-family:"Playball",cursive;font-size:56px;line-height:1;color:var(--ink)}
  .title--one{left:70px;top:440px}
  .title--two{left:140px;top:497px}
  .subtitle{left:0;width:500px;top:574px;text-align:center;font-size:16.5px;font-weight:500;line-height:21px}
  .weeks{left:0;width:500px;top:652px;text-align:center;font-size:23px;font-weight:700;letter-spacing:.5px}
  .cost{left:0;width:500px;top:687px;display:flex;justify-content:center}
  .cost__label{background:var(--blue);color:var(--white);font-size:19px;font-weight:500;padding:2px 18px;border-radius:3px 0 0 3px;letter-spacing:1px}
  .cost__value{background:var(--mint);font-size:19px;font-weight:500;padding:2px 12px;border-radius:0 3px 3px 0}
  .group-size{left:0;width:500px;top:727px;text-align:center;font-size:19.5px;font-weight:500}
  .topics{left:24px;top:762px;width:452px;height:226px;background:var(--mint);border:1.5px solid var(--blue);border-radius:4px}
  .topics__label{left:0;width:500px;top:748px;display:flex;justify-content:center}
  .topics__label span{background:var(--blue);color:var(--white);font-family:"Roboto Condensed",sans-serif;font-size:20px;padding:0 14px;border-radius:12px;line-height:26px}
  .topics__col{list-style:none;font-family:"Roboto Condensed",sans-serif;font-weight:300;font-size:16px;color:#222;top:20px}
  .topics__col--left{left:10px;width:210px}
  .topics__col--right{left:241px;width:210px}
  .topics__col li{position:relative;padding-left:18px;line-height:21px;margin-bottom:10.5px}
  .topics__col li::before{content:"";position:absolute;left:1px;top:6px;width:7px;height:7px;border:1px solid var(--blue);border-radius:1px}
  .topics__divider{left:232px;top:18px;width:1px;height:185px;background:var(--blue);opacity:.6}
  .more-info{left:0;width:500px;top:1000px;text-align:center;font-size:16.5px;font-weight:600;letter-spacing:.2px}
  .footer-wave{left:0;top:1010px;width:500px;height:115px}
  .footer-name{left:0;width:500px;top:1067px;text-align:center;color:var(--white);font-size:17px}
  .footer-name b{font-weight:600}
  .footer-contacts{left:0;width:500px;top:1094px;display:flex;justify-content:center;gap:14px;color:var(--white);font-size:15px;font-weight:500;align-items:center}
  .contact{display:flex;align-items:center;gap:5px}

  /* back */
  .quote-box{left:30px;top:37px;width:438px;height:344px;border:1.5px solid var(--blue);border-radius:8px}
  .quote-mark{font-family:Georgia,serif;font-size:62px;font-weight:700;color:var(--blue);line-height:1;background:var(--mint-card);padding:0 4px;height:34px;overflow:hidden}
  .quote-mark--open{left:40px;top:16px}
  .quote-mark--close{left:420px;top:363px}
  .quote-text{left:40px;top:57px;width:419px;font-size:14.3px;line-height:18.8px;text-align:justify}
  .quote-text p+p{margin-top:24px}
  .quote-sign{right:44px;top:345px;font-size:14.5px}
  .quote-sign b{font-weight:600}
  .bio-photo{left:30px;top:406px;width:440px;height:255px;border-radius:8px;
    background:linear-gradient(180deg,#7e8a72 0%,#b7a48a 22%,#c9b8a4 45%,#a59a8e 70%,#8a8178 100%)}
  .bio{left:40px;top:677px;width:419px;font-size:14.3px;line-height:18.8px;text-align:justify}
  .bio p+p{margin-top:12px}
  .back-divider{left:248px;top:812px;width:1px;height:140px;background:var(--blue);opacity:.5}
  .brand--back{left:70px;top:850px;width:170px;justify-content:flex-start;gap:8px}
  .brand--back .brand__dot{width:26px;height:26px}
  .brand--back .brand__name{font-size:16px}
  .counselor{left:268px;top:868px;font-family:"Roboto Condensed",sans-serif;font-size:23px;letter-spacing:-.5px}
  .credentials{left:272px;top:897px;list-style:none;font-size:14.5px;line-height:18px;color:var(--green-text)}
  .credentials li{position:relative;padding-left:14px;margin-bottom:13px}
  .credentials li::before{content:"";position:absolute;left:0;top:6px;width:6px;height:6px;border-radius:50%;background:var(--blue)}
  .headshot{left:34px;top:966px;width:140px;height:140px;border-radius:50%;border:5px solid var(--white);box-shadow:0 0 0 2px var(--teal);
    background:radial-gradient(circle at 50% 40%,#e8cfa0 0%,#c9a86a 45%,#4a5a6a 100%)}
  .more-info--back{left:183px;top:985px;width:300px;text-align:left;font-size:16.5px}
  .back-contacts{left:192px;top:1070px;color:var(--white);font-size:15px;font-weight:500}
  .back-contacts .contact{margin-bottom:9px}
</style>
</head>
<body>

<section class="card card--front">
  <div class="abs hero-photo" role="img" aria-label="Woman in a white shirt sitting on beach rocks, seen from behind, looking out over the sea"></div>
  <div class="abs brand">
    <span class="brand__dot"></span>
    <span class="brand__name">Quiet Harbor<br>Counseling</span>
  </div>
  <svg class="abs hero-curve" viewBox="0 0 500 70" preserveAspectRatio="none">
    <path d="M0 22 Q250 -12 500 30 L500 70 L0 70 Z" fill="var(--teal)"/>
    <path d="M0 34 Q250 2 500 42 L500 70 L0 70 Z" fill="var(--white)"/>
  </svg>

  <h1 class="abs title title--one">Mending the</h1>
  <h1 class="abs title title--two">Weary Spirit</h1>
  <p class="abs subtitle">Women's Trauma &amp; Loss Group Led by<br>Licensed Professional Counselor,<br>Lena Marsh Pruitt</p>
  <p class="abs weeks">10 WEEK GROUP</p>
  <div class="abs cost"><span class="cost__label">COST</span><span class="cost__value">$35 session</span></div>
  <p class="abs group-size">Group size limited to 10 participants</p>

  <div class="abs topics">
    <ul class="abs topics__col topics__col--left">
      <li>What is Trauma?</li>
      <li>How Trauma Affects Us</li>
      <li>Creating a Feeling of Safety</li>
      <li>Managing Trauma Triggers</li>
      <li>Importance of Self Care</li>
      <li>Healthy vs. Unhealthy<br>Coping</li>
    </ul>
    <span class="abs topics__divider"></span>
    <ul class="abs topics__col topics__col--right">
      <li>Guilt, Shame, and Blame</li>
      <li>Victim vs. Victimized</li>
      <li>Grieving through Loss</li>
      <li>Anger and Forgiveness</li>
      <li>Imagining a Better Future</li>
    </ul>
  </div>
  <div class="abs topics__label"><span>Topics Include:</span></div>

  <p class="abs more-info">For More Information, Contact:</p>
  <svg class="abs footer-wave" viewBox="0 0 500 115" preserveAspectRatio="none">
    <path d="M0 16 Q250 38 500 14 L500 115 L0 115 Z" fill="var(--teal)"/>
    <path d="M0 22 Q250 44 500 22 L500 115 L0 115 Z" fill="var(--white)"/>
    <path d="M0 30 Q250 46 500 28 L500 115 L0 115 Z" fill="var(--blue)"/>
  </svg>
  <p class="abs footer-name"><b>Lena Marsh Pruitt</b>, LPC, LMFT</p>
  <div class="abs footer-contacts">
    <span class="contact">
      <svg width="13" height="13" viewBox="0 0 24 24"><path d="M6.6 10.8a15 15 0 0 0 6.6 6.6l2.2-2.2a1 1 0 0 1 1-.25 11.4 11.4 0 0 0 3.6.57 1 1 0 0 1 1 1V20a1 1 0 0 1-1 1A17 17 0 0 1 3 4a1 1 0 0 1 1-1h3.5a1 1 0 0 1 1 1c0 1.25.2 2.45.57 3.57a1 1 0 0 1-.25 1z" fill="currentColor"/></svg>
      (555) 318-4926</span>
    <span class="contact">
      <svg width="12" height="10" viewBox="0 0 24 18"><rect x="0" y="0" width="24" height="18" rx="2" fill="currentColor"/><path d="M1 1l11 9 11-9" stroke="var(--blue)" stroke-width="2" fill="none"/></svg>
      lena@calmwatersguide.example</span>
  </div>
</section>

<section class="card card--back">
  <div class="abs quote-box"></div>
  <span class="abs quote-mark quote-mark--open">“</span>
  <div class="abs quote-text">
    <p>Life hurts and does not seem fair. So what do you do when you are faced with an event in your life that knocks you off your feet? It seems no one understands what you are feeling and no one knows just what to say. It is tempting to pull away and isolate or put up a mask and pretend everything is OK.</p>
    <p>It is my desire you know that you are not alone! There are others who understand the feelings you are going through and offer a safe place for encouraging support. I want to invite you to embark on a courageous journey of healing where you will not only learn how to "survive" after trauma and loss, but instead, learn that you can once again "thrive"!</p>
  </div>
  <p class="abs quote-sign">- <b>Lena Marsh Pruitt</b>, <i>LPC, LMFT</i></p>
  <span class="abs quote-mark quote-mark--close">”</span>

  <div class="abs bio-photo" role="img" aria-label="The counselor sitting on a rock on a sandy beach at sunset"></div>
  <div class="abs bio">
    <p>Lena Marsh Pruitt is a Licensed Professional Counselor and Licensed Marriage and Family Therapist. She is the owner of Quiet Harbor Counseling Services located in Tulsa, OK.</p>
    <p>Lena is a trauma survivor herself and understands firsthand the unique challenges that can arise on the journey to healing.</p>
  </div>

  <span class="abs back-divider"></span>
  <div class="abs brand brand--back">
    <span class="brand__dot"></span>
    <span class="brand__name">Quiet Harbor<br>Counseling</span>
  </div>
  <p class="abs counselor">Lena Pruitt, LPC-S, LMFT</p>
  <ul class="abs credentials">
    <li>Licensed Professional<br>Counselor</li>
    <li>Licensed Marriage &amp;<br>family Therapist</li>
  </ul>

  <svg class="abs footer-wave" style="top:985px;height:140px" viewBox="0 0 500 140" preserveAspectRatio="none">
    <path d="M0 18 Q250 44 500 12 L500 140 L0 140 Z" fill="var(--teal)"/>
    <path d="M0 24 Q250 48 500 18 L500 140 L0 140 Z" fill="var(--white)"/>
    <path d="M0 32 Q250 52 500 26 L500 140 L0 140 Z" fill="var(--blue)"/>
  </svg>
  <p class="abs more-info more-info--back">For More Information, Contact:</p>
  <div class="abs headshot" role="img" aria-label="Head-and-shoulders portrait of the counselor"></div>
  <div class="abs back-contacts">
    <p class="contact">
      <svg width="13" height="13" viewBox="0 0 24 24"><path d="M6.6 10.8a15 15 0 0 0 6.6 6.6l2.2-2.2a1 1 0 0 1 1-.25 11.4 11.4 0 0 0 3.6.57 1 1 0 0 1 1 1V20a1 1 0 0 1-1 1A17 17 0 0 1 3 4a1 1 0 0 1 1-1h3.5a1 1 0 0 1 1 1c0 1.25.2 2.45.57 3.57a1 1 0 0 1-.25 1z" fill="currentColor"/></svg>
      (555) 318-4926</p>
    <p class="contact">
      <svg width="12" height="10" viewBox="0 0 24 18"><rect x="0" y="0" width="24" height="18" rx="2" fill="currentColor"/><path d="M1 1l11 9 11-9" stroke="var(--blue)" stroke-width="2" fill="none"/></svg>
      lena@calmwatersguide.example</p>
  </div>
</section>

</body>
</html>
```